Kampfsport Außenwerbung
Zielgruppe
Kampfsportschule für Kinder, Jugendliche und Erwachsene. Sportarten: Kick-Boxen, Jiu-Jitsu und Tricking
Aufgabenstellung
Ich bräuchte für meine Schaufenster eine schöne Außenwerbung. Beworben werden sollen alle meine Sportarten. Ich lade meinen Flyer hoch, damit im ähnlichen Stil gearbeitet werden kann. Außerdem auch noch andere Beispiele an denen man sich orientieren kann, sowie mein Logo und meine Fensterfront.

```html
<!DOCTYPE html>
<html lang="de">
<head>
<meta charset="utf-8">
<title>Martial Arts Borq – Schaufensterwerbung</title>
<link href="https://fonts.googleapis.com/css2?family=Rubik:wght@400;500;700;800;900&family=Russo+One&family=Cormorant+Garamond:wght@500&display=swap" rel="stylesheet">
<style>
  :root{
    --bg:#e4e4e4;
    --frame:#f4f4f4;
    --char-1:#2c2c2c;
    --char-2:#141414;
    --red:#a3121f;
    --red-dark:#6e0c15;
    --red-bright:#d4162a;
    --white:#ffffff;
    --grey-cell:#4a4a4a;
    --ink:#1a1a1a;
  }
  *{box-sizing:border-box;margin:0;padding:0}
  html,body{width:900px;height:1200px;overflow:hidden}
  body{background:var(--bg);font-family:"Rubik",sans-serif;position:relative;color:var(--white)}

  .storefront{position:absolute;left:20px;top:350px;width:860px;height:500px}

  /* sign above the doors */
  .shop-sign{position:absolute;left:258px;top:0;width:270px;height:104px;background:var(--white);
    border-top:10px solid #2e2e2e;border-bottom:10px solid #2e2e2e;display:flex;align-items:center;padding:0 12px;gap:10px}
  .shop-sign::before,.shop-sign::after{content:"";position:absolute;left:0;right:0;height:2px;background:var(--red)}
  .shop-sign::before{top:4px}.shop-sign::after{bottom:4px}
  .brand-mark{display:flex;align-items:center;gap:4px;font-family:"Rubik",sans-serif;font-weight:700;color:var(--red);font-size:10px;line-height:1.05;width:78px}
  .brand-mark .dot{flex:none;width:10px;height:10px;border-radius:50%;background:var(--red)}
  .sign-text{text-align:center;flex:1}
  .sign-title{font-family:"Russo One",sans-serif;font-style:italic;color:var(--ink);font-size:15px;letter-spacing:.5px}
  .sign-sub{font-family:"Cormorant Garamond",serif;color:var(--ink);font-size:13px;line-height:1.15;margin-top:3px}

  .panels{position:absolute;left:0;top:124px;width:860px;height:360px;display:flex;gap:8px}
  .panel{position:relative;height:100%;overflow:hidden;border:4px solid var(--frame);
    background:radial-gradient(ellipse at 50% 35%,#3a3a3a 0%,var(--char-1) 40%,var(--char-2) 100%)}
  .panel svg.bands{position:absolute;inset:0;width:100%;height:100%}
  .kick{width:103px}.jiu{width:116px}.door-l{width:136px}.door-r{width:142px}.trick{width:159px}.plan{width:164px}

  .photo{position:absolute;background:radial-gradient(ellipse at 50% 45%,#5a5a5a 0%,#2e2e2e 55%,rgba(30,30,30,0) 75%)}
  .photo.kid-red{background:radial-gradient(ellipse at 50% 50%,#6b2a30 0%,#3a2a2c 45%,rgba(30,30,30,0) 72%)}
  .photo.kid-white{background:radial-gradient(ellipse at 50% 50%,#e8e8e8 0%,#9a9a9a 30%,rgba(40,40,40,0) 68%)}

  .slant{position:absolute;left:0;right:0;text-align:center;transform:rotate(-8deg);font-weight:800;text-transform:uppercase;line-height:1}
  .kick .slant{bottom:46px;font-size:15px}
  .jiu .slant{top:18px;font-size:17px}
  .jiu .slant small{display:block;font-size:6px;font-weight:700;text-transform:none;margin-top:2px;line-height:1.2}
  .trick .slant{bottom:34px;font-size:22px}
  .trick .slant small{display:block;font-size:7px;font-weight:700;text-transform:none;margin-top:3px}
  .plan .slant{top:34px;font-size:20px;transform:rotate(-9deg)}

  .door-l .brand-mark{position:absolute;left:26px;top:128px;color:var(--red-bright);width:auto;font-size:11px}
  .door-title{position:absolute;left:0;right:0;text-align:center;font-weight:800;font-size:14px;line-height:1.1;text-transform:uppercase}
  .door-l .door-title{top:178px}
  .door-r .door-title{top:36px;font-size:15px}
  .rule{position:absolute;left:0;right:0;top:84px;height:1px;background:var(--red-bright)}
  .info-head{position:absolute;left:8px;right:4px;top:124px;font-size:9px;font-weight:500}
  .contact{position:absolute;left:10px;display:flex;align-items:center;gap:6px;font-size:7px;font-weight:500}
  .contact svg{width:10px;height:10px;flex:none}
  .contact.mail{top:150px}.contact.phone{top:170px}
  .lead{position:absolute;left:0;right:0;top:228px;text-align:center;font-size:10px;font-weight:700;line-height:1.35;text-transform:uppercase}

  .schedule{position:absolute;left:4px;top:142px;width:148px;border-collapse:collapse;table-layout:fixed;font-size:4.3px;line-height:1.15}
  .schedule th{background:var(--ink);font-weight:700;height:11px;text-transform:uppercase}
  .schedule th.time-col{width:14px}
  .schedule td{height:17px;padding:1px;border:.5px solid #fff;vertical-align:middle;background:#2a2a2a}
  .schedule td.time{background:var(--red-bright);text-align:center;font-weight:500}
  .schedule td.jj{background:var(--red-bright)}
  .schedule td.alt{background:var(--grey-cell)}
  .schedule td.free{background:#f2f2f2}
  .schedule .clock{display:inline-block;width:6px;height:6px;border:1px solid #fff;border-radius:50%}
  .call{position:absolute;left:0;right:0;top:272px;text-align:center;font-weight:700;font-size:11px;line-height:1.3}
</style>
</head>
<body>
<main class="storefront">

  <header class="shop-sign">
    <div class="brand-mark"><span class="dot"></span><span>Martial Arts Borq</span></div>
    <div class="sign-text">
      <div class="sign-title">MARTIAL ARTS BORQ</div>
      <div class="sign-sub">Kampfsport &amp;<br>Selbstverteidigung</div>
    </div>
  </header>

  <section class="panels">

    <article class="panel kick">
      <svg class="bands" viewBox="0 0 95 352" preserveAspectRatio="none">
        <polygon points="0,275 95,245 95,320 0,352" fill="var(--red)"/>
        <polygon points="0,262 95,232 95,240 0,270" fill="var(--red-dark)"/>
      </svg>
      <div class="photo kid-red" style="left:0;top:10px;width:95px;height:250px" role="img" aria-label="Kind im Kickbox-Outfit mit rotem Kopfschutz und pinken Handschuhen beim hohen Tritt"></div>
      <div class="slant">Kick-Boxen</div>
    </article>

    <article class="panel jiu">
      <svg class="bands" viewBox="0 0 108 352" preserveAspectRatio="none">
        <polygon points="0,30 108,0 108,70 0,100" fill="var(--red)"/>
        <polygon points="0,320 108,300 108,352 0,352" fill="var(--red-dark)"/>
      </svg>
      <div class="slant">Jiu-Jitsu<small>Für Kinder, Jugendliche<br>und Erwachsene!</small></div>
      <div class="photo kid-white" style="left:4px;top:105px;width:100px;height:240px" role="img" aria-label="Mädchen im weißen Jiu-Jitsu-Anzug mit gelbem Gürtel in Kampfhaltung"></div>
    </article>

    <article class="panel door-l">
      <svg class="bands" viewBox="0 0 128 352" preserveAspectRatio="none">
        <polygon points="0,315 128,290 128,320 0,345" fill="var(--red)"/>
        <polygon points="0,345 128,320 128,352 0,352" fill="var(--red-dark)"/>
      </svg>
      <div class="brand-mark"><span class="dot"></span><span>Martial Arts Borq</span></div>
      <div class="door-title">Martial Arts<br>Borq</div>
    </article>

    <article class="panel door-r">
      <svg class="bands" viewBox="0 0 134 352" preserveAspectRatio="none">
        <polygon points="0,320 134,295 134,352 0,352" fill="var(--red-dark)"/>
      </svg>
      <div class="door-title">Martial Arts<br>Borq</div>
      <div class="rule"></div>
      <div class="info-head">INFO &amp; PROBETRAINING</div>
      <div class="contact mail">
        <svg viewBox="0 0 10 10"><rect x="0.5" y="1.5" width="9" height="7" fill="none" stroke="var(--red-bright)"/><polyline points="0.5,1.5 5,5.5 9.5,1.5" fill="none" stroke="var(--red-bright)"/></svg>
        <span>info@martial-arts-borq.de</span>
      </div>
      <div class="contact phone">
        <svg viewBox="0 0 10 10"><circle cx="5" cy="5" r="4.4" fill="none" stroke="var(--red-bright)"/><path d="M3.3 2.8 4.3 2.6 4.8 3.9 4.1 4.4Q4.6 5.6 5.7 6.1L6.2 5.4 7.4 5.9 7.2 6.9Q4.2 7 3.3 2.8Z" fill="var(--red-bright)"/></svg>
        <span>0152 / 3000 1847</span>
      </div>
      <div class="lead">Leitung:<br>Timo Borq</div>
    </article>

    <article class="panel trick">
      <svg class="bands" viewBox="0 0 151 352" preserveAspectRatio="none">
        <polygon points="0,290 151,255 151,330 0,352" fill="var(--red)"/>
        <polygon points="0,278 151,243 151,252 0,287" fill="var(--red-dark)"/>
      </svg>
      <div class="photo kid-red" style="left:10px;top:8px;width:131px;height:270px" role="img" aria-label="Mädchen in schwarzer Trainingskleidung mit gelbem Gürtel beim Spagat im Stand"></div>
      <div class="slant">Tricking<small>Wir machen Dich Stark!</small></div>
    </article>

    <article class="panel plan">
      <svg class="bands" viewBox="0 0 156 352" preserveAspectRatio="none">
        <polygon points="0,50 156,10 156,75 0,115" fill="var(--red)"/>
        <polygon points="0,0 40,0 0,20" fill="var(--red-dark)"/>
        <polygon points="156,0 156,10 120,0" fill="var(--red-dark)"/>
      </svg>
      <div class="slant">Trainings-<br>plan</div>
      <table class="schedule">
        <thead>
          <tr><th class="time-col"><span class="clock"></span></th><th>Montag</th><th>Dienstag</th><th>Mittwoch</th><th>Donnerstag</th><th>Freitag</th></tr>
        </thead>
        <tbody>
          <tr><td class="time">15:00<br>15:50</td><td>Kick-Boxen<br>3-5 Jahre</td><td class="jj">Jiu-Jitsu<br>3-6 Jahre</td><td>Kick-Boxen<br>3-5 Jahre</td><td class="jj">Jiu-Jitsu<br>3-6 Jahre</td><td class="free"></td></tr>
          <tr><td class="time">16:00<br>16:50</td><td>Kick-Boxen<br>6-7 Jahre</td><td class="jj">Jiu-Jitsu<br>7-12 Jahre</td><td>Kick-Boxen<br>6-7 Jahre</td><td class="jj">Jiu-Jitsu<br>7-12 Jahre</td><td>Kick-Boxen<br>3-5 Jahre</td></tr>
          <tr><td class="time">17:00<br>17:50</td><td>Kick-Boxen<br>8-10 Jahre</td><td class="alt">Tricking<br>ab 6 Jahre</td><td>Kick-Boxen<br>8-10 Jahre</td><td class="alt">Tricking<br>ab 6 Jahre</td><td>Kick-Boxen<br>ab 7 Jahre<br>Ab Gelbgurt</td></tr>
          <tr><td class="time">18:15<br>19:15</td><td>Kick-Boxen<br>10-12 Jahre</td><td class="alt">Kick-Boxen<br>U25 Gruppe</td><td>Kick-Boxen<br>10-12 Jahre</td><td class="alt">Kick-Boxen<br>U25 Gruppe</td><td class="free"></td></tr>
          <tr><td class="time">19:30<br>21:00</td><td>Kick-Boxen<br>ab 13 Jahre</td><td class="free"></td><td>Kick-Boxen<br>ab 13 Jahre</td><td class="free"></td><td class="free"></td></tr>
        </tbody>
      </table>
      <div class="call">Jetzt Probetermin<br>vereinbaren!</div>
    </article>

  </section>
</main>
</body>
</html>
```